Bourbon label design for bourbon brand. Looking to freshen our current label.

I need a Bourbon label design for our rebranded Bourbon bottle. Label should include picture of our horse and our logo on the bottle. Front Label is 3.5 inches wide and 6 inches tall, back label is 4 inches tall and 3 inches wide. Back label can be a simple plain logo like the one in the brief. I have included a design of our current bottle and label. We want to stay close to the current color schemes but want a fresh rebrand of the design. The label needs to be the correct size on a tall bottle like pictured.

Target Market(s)

Our Bourbon members, 30-50 year old males

Requirements
Must have
• Picture of our horse, our B logo , straight Bourbon whiskey on the front. Room to edit text on the back label.

```html
<!DOCTYPE html>
<html lang="en">
<head>
<meta charset="utf-8">
<title>Nightfall Straight Bourbon Labels</title>
<link href="https://fonts.googleapis.com/css2?family=Bebas+Neue&family=Oswald:wght@500;600&family=Space+Grotesk:wght@300;400;500;600&display=swap" rel="stylesheet">
<style>
:root{
  --paper:#ffffff;
  --stage:#6f6f6e;
  --ink:#111111;
  --label-black:#0b0b0b;
  --gold:#c9a552;
  --gold-light:#efe19a;
  --white:#ffffff;
  --back-paper:#efefef;
  --text-dark:#1d1d1d;
}
*{margin:0;padding:0;box-sizing:border-box}
html,body{width:1200px;height:981px;overflow:hidden}
body{position:relative;background:var(--paper);font-family:"Space Grotesk",sans-serif}
.stage-right{position:absolute;left:631px;top:0;width:569px;height:981px;background:var(--stage)}

/* Front label */
.front-label{position:absolute;left:78px;top:84px;width:475px;height:813px;overflow:hidden;
  background:linear-gradient(180deg,#2b2b2b 0%,#1a1a1a 35%,#0a0a0a 70%,#050505 100%)}
.front-bg-photo{position:absolute;left:30px;top:0;width:445px;height:430px;
  background:radial-gradient(ellipse at 55% 35%,rgba(120,120,120,.35),rgba(40,40,40,0) 70%)}
.gold-band{position:absolute;left:0;width:475px;height:20px}
.gold-band.top{top:0}
.gold-band.bottom{bottom:0}
.brand-mark{position:absolute;left:0;width:100%;top:118px;text-align:center;
  font-family:"Oswald",sans-serif;font-weight:600;font-size:20px;letter-spacing:6px;color:var(--white)}
.brand-title{position:absolute;left:0;width:100%;top:232px;text-align:center;
  font-family:"Bebas Neue",sans-serif;font-size:112px;line-height:1;letter-spacing:4px;color:var(--gold)}
.spirit-type{position:absolute;left:0;width:100%;top:344px;text-align:center;
  font-family:"Bebas Neue",sans-serif;font-size:30px;letter-spacing:1px;color:var(--white)}
.horse-photo{position:absolute;left:123px;top:414px;width:229px;height:393px;border-radius:40% 40% 20% 20%;
  background:radial-gradient(ellipse at 50% 45%,#9a9a9a 0%,#6a6a6a 45%,#2a2a2a 80%,rgba(20,20,20,0) 100%)}
.spec-box{position:absolute;left:25px;top:653px;width:84px;height:133px;border:1px solid #555;border-radius:4px;
  background:#000;padding:7px 4px;text-align:center;font-size:10px;font-weight:500;color:var(--white)}
.spec-box .spec-name{display:block;height:13px;line-height:13px}
.spec-box .spec-field{display:block;height:18px;margin:4px 0 8px;background:var(--white);color:var(--ink);line-height:18px}
.badge{position:absolute;left:354px;top:699px;width:92px;height:76px}
.badge-text{position:absolute;left:0;width:92px;text-align:center;font-family:"Bebas Neue",sans-serif;
  font-size:17px;color:var(--white);letter-spacing:.5px}

/* Back label */
.back-label{position:absolute;left:712px;top:219px;width:407px;height:542px;overflow:hidden;
  background:var(--back-paper);color:var(--text-dark);text-align:center}
.back-bg-photo{position:absolute;left:40px;top:0;width:340px;height:440px;
  background:radial-gradient(ellipse at 55% 40%,rgba(150,150,150,.35),rgba(239,239,239,0) 70%)}
.back-brand{position:absolute;left:0;width:100%;top:84px;font-weight:600;font-size:15px;line-height:15px;color:var(--ink)}
.back-brand small{display:block;font-size:6px;font-weight:400;letter-spacing:3px;margin-top:3px}
.series-title{position:absolute;left:0;width:100%;top:142px;font-weight:500;font-size:20.5px;line-height:29px}
.story{position:absolute;left:36px;width:335px;font-weight:500;font-size:11px;line-height:14.6px}
.story.one{top:235px}
.story.two{top:305px}
.bottler{position:absolute;left:20px;width:367px;top:364px;font-weight:500;font-size:12px;line-height:16.4px}
.site{position:absolute;left:0;width:100%;top:400px;font-weight:600;font-size:18px}
.warning{position:absolute;left:25px;width:358px;top:427px;font-weight:300;font-size:11px;line-height:14.7px;text-align:justify}
.volume{position:absolute;left:0;width:100%;top:510px;font-weight:600;font-size:17px}
</style>
</head>
<body>
<div class="stage-right"></div>

<section class="front-label">
  <div class="front-bg-photo" role="img" aria-label="Faint close-up photo of racehorse and jockey"></div>
  <svg class="gold-band top" viewBox="0 0 475 20" preserveAspectRatio="none">
    <defs><linearGradient id="goldA" x1="0" x2="1"><stop offset="0" stop-color="#b8913f"/><stop offset=".45" stop-color="#efe19a"/><stop offset="1" stop-color="#b8913f"/></linearGradient></defs>
    <polygon points="0,0 475,0 475,1 0,17" fill="url(#goldA)"/>
  </svg>
  <div class="brand-mark">NIGHTFALL</div>
  <div class="brand-title">NIGHTFALL</div>
  <div class="spirit-type">STRAIGHT BOURBON WHISKEY</div>
  <div class="horse-photo" role="img" aria-label="Photo of the racehorse with jockey galloping toward viewer"></div>
  <div class="spec-box">
    <span class="spec-name">ALC/VOL</span><span class="spec-field"></span>
    <span class="spec-name">AGED</span><span class="spec-field">Years</span>
    <span class="spec-name">BARREL NO</span><span class="spec-field"></span>
  </div>
  <div class="badge">
    <svg width="92" height="76" viewBox="0 0 92 76" fill="none" stroke="#fff" stroke-width="1">
      <line x1="3" y1="0" x2="3" y2="76"/><line x1="89" y1="0" x2="89" y2="76"/>
      <line x1="0" y1="9" x2="92" y2="9"/><line x1="0" y1="38" x2="92" y2="38"/><line x1="0" y1="67" x2="92" y2="67"/>
    </svg>
    <div class="badge-text" style="top:13px">SINGLE BARREL</div>
    <div class="badge-text" style="top:42px">CASK STRENGTH</div>
  </div>
  <svg class="gold-band bottom" viewBox="0 0 475 20" preserveAspectRatio="none">
    <defs><linearGradient id="goldB" x1="0" x2="1"><stop offset="0" stop-color="#b8913f"/><stop offset=".5" stop-color="#efe19a"/><stop offset="1" stop-color="#b8913f"/></linearGradient></defs>
    <polygon points="0,4 475,18 475,20 0,20" fill="url(#goldB)"/>
  </svg>
</section>

<section class="back-label">
  <div class="back-bg-photo" role="img" aria-label="Faint photo of racehorse and jockey"></div>
  <div class="back-brand">NIGHTFALL<br>CASK<small>COMPANY</small></div>
  <div class="series-title">Winners Series<br>Silver Tempest Edition<br>Single Barrel No.45</div>
  <p class="story one">The Nightfall Racing Winners Series honors the horses who have brought home victories for our stable. This edition celebrates Silver Tempest and her maiden victory on May 28, 2021.</p>
  <p class="story two">Raise a glass to her incredible career with this non-chill filtered single barrel crafted in her honor. Here’s to Silver Tempest a true champion!</p>
  <p class="bottler">Bottled by Riverbend Whiskey Co., Louisville, Kentucky<br>Distilled in Bardstown. Kentucky</p>
  <div class="site">NIGHTFALL-GROUP.COM</div>
  <p class="warning">GOVERNMENT WARNING: (1) According to the Surgeon General, women should not drink alcoholic beverages during pregnancy because of the risk of birth defects. (2) Consumption of alcoholic beverages impairs your ability to drive a car or operate machinery, and may cause health problems.</p>
  <div class="volume">750ML</div>
</section>
</body>
</html>
```